Brightline Energy Product Distribution Brochure

We are looking to have our current brochure for our customers completely redesigned...the idea is to present the relevant information in an attractive way . Our website is brightlineenergyco.example where you can find more information about us. We have included a file with a rough idea of the page order and what each should include but feel free to adapt based on design. The example provided is only for context and doesnt have to be maintained. We will be using the brochure both digitally and in print form. As long as it reads easily and is eye catching, the design can be horizontal or vertical.Final deliverable should be indesign file.

"Our Brands" page: should be limited to one page (space being enough) where it has the header for each one (for example diesel generators) space for one or two lines of text and then the corresponding logos for each of the five categories
Updates

For those asking: the "our brands" page should be a single page layout where there is a header with the corresponding section and space for maybe one line of text followed by the two logos for that category. Each of the product pages should be similar in fashion to the one in the document attached: a photo of the product with some white space and space for the text to be included. We will be posting additional examples today

Target Market(s)

We want to present it to customers both digitally and in print so they can see our products

Industry/Entity Type

Power Generation

Font styles to use
Serif

Requirements
Must have
• Eye catching and able to present the information in a presentable fashion. Rest is up to you.
Nice to have
• Should incorporate the colors of our logo but can also add other depending on design

```html
<!DOCTYPE html>
<html lang="en">
<head>
<meta charset="utf-8">
<title>Brightline Energy Brochure Spreads</title>
<link rel="stylesheet" href="https://fonts.googleapis.com/css2?family=Oswald:wght@600;700&family=Roboto+Condensed:ital,wght@0,700;1,700&family=Roboto:wght@400&display=swap">
<style>
:root{
  --bg:#f1f2f4;
  --yellow:#f7cf16;
  --yellow-deep:#f3b01a;
  --orange:#f5a623;
  --charcoal:#4a4544;
  --charcoal-dark:#3b3736;
  --white:#ffffff;
  --ink:#3a3a3a;
}
*{margin:0;padding:0;box-sizing:border-box}
html,body{width:1200px;height:1200px;overflow:hidden;background:var(--bg)}
.canvas{position:relative;width:1200px;height:1200px}
.spread{position:absolute;overflow:hidden;background:var(--white);box-shadow:0 2px 6px rgba(0,0,0,.18)}
.spread--top{left:183px;top:38px;width:835px;height:535px}
.spread--bottom{left:180px;top:630px;width:842px;height:540px}
.spread-art{position:absolute;inset:0}
.vertical-title{position:absolute;writing-mode:vertical-rl;transform:rotate(180deg);font-family:"Oswald",sans-serif;font-weight:700;letter-spacing:1px;line-height:1;white-space:nowrap}
.title-alternator{left:17px;top:34px;height:444px;font-size:57px;color:var(--white)}
.title-controllers{left:436px;top:139px;height:335px;font-size:50px;color:var(--yellow);letter-spacing:4px}
.title-transfer{left:16px;top:36px;height:442px;font-size:46px;letter-spacing:0;color:var(--white)}
.page-num{position:absolute;font-family:"Roboto Condensed",sans-serif;font-style:italic;font-weight:700;font-size:10px;letter-spacing:.5px}
.photo{position:absolute}
.spec-list{position:absolute;font-family:"Roboto",sans-serif;font-size:8.2px;line-height:10.85px;color:var(--ink);list-style:none}
.distributors-title{position:absolute;left:480px;top:32px;width:284px;text-align:center;font-family:"Roboto Condensed",sans-serif;font-style:italic;font-weight:700;font-size:33px;line-height:40px;color:var(--orange)}
.products-label{position:absolute;left:474px;top:136px;font-family:"Roboto Condensed",sans-serif;font-weight:700;font-size:10px;color:var(--orange)}
.product-list{position:absolute;left:490px;top:171px;list-style:none;font-family:"Roboto Condensed",sans-serif;font-weight:700;font-size:10px;color:var(--orange)}
.product-list li{height:27.2px;position:relative;padding-left:14px}
.product-list li::before{content:"";position:absolute;left:0;top:4px;width:5px;height:5px;border-radius:50%;background:var(--orange)}
.team-photo{position:absolute;left:434px;top:414px;width:232px;height:97px;border:2px solid var(--orange);background:linear-gradient(135deg,#6f6b66,#b9bab5 55%,#4b4947)}
</style>
</head>
<body>
<main class="canvas">

  <section class="spread spread--top">
    <svg class="spread-art" width="835" height="535" viewBox="0 0 835 535">
      <defs>
        <linearGradient id="yellowA" x1="0" y1="0" x2="1" y2="1">
          <stop offset="0" stop-color="#f8d21b"/><stop offset="1" stop-color="#f3b21a"/>
        </linearGradient>
      </defs>
      <rect x="0" y="0" width="417" height="535" fill="#fff"/>
      <polygon points="0,0 341,0 61,535 0,535" fill="url(#yellowA)"/>
      <rect x="417" y="0" width="418" height="535" fill="var(--charcoal)"/>
      <polygon points="609,535 835,194 835,535" fill="url(#yellowA)"/>
    </svg>

    <h2 class="vertical-title title-alternator">ALTERNATOR PARTS</h2>
    <div class="photo" role="img" aria-label="Automatic voltage regulator board product photo" style="left:281px;top:166px;width:116px;height:106px;background:linear-gradient(160deg,#4a4d55,#22242a 70%,#eef0f2 70%)"></div>
    <div class="photo" role="img" aria-label="Industrial alternator product photo" style="left:127px;top:320px;width:230px;height:192px;border-radius:30px 10px 10px 60px;background:linear-gradient(135deg,#5c6062,#2f3335 60%,#1f2224)"></div>
    <span class="page-num" style="left:17px;top:509px;color:var(--charcoal-dark)">PAGE 10</span>

    <h2 class="vertical-title title-controllers">CONTROLLERS</h2>
    <div class="photo" role="img" aria-label="Generator control panel cabinet product photo" style="left:551px;top:35px;width:186px;height:467px;background:linear-gradient(90deg,#3c3f42,#55595c 45%,#3a3d40)"></div>
    <span class="page-num" style="right:18px;top:509px;color:var(--white)">PAGE 11</span>
  </section>

  <section class="spread spread--bottom">
    <svg class="spread-art" width="842" height="540" viewBox="0 0 842 540">
      <defs>
        <linearGradient id="yellowB" x1="0" y1="0" x2="1" y2="1">
          <stop offset="0" stop-color="#f8d21b"/><stop offset="1" stop-color="#f3b01a"/>
        </linearGradient>
      </defs>
      <polygon points="0,0 336,0 84,540 0,540" fill="url(#yellowB)"/>
      <polygon points="604,540 842,86 842,540" fill="var(--charcoal)"/>
      <line x1="611" y1="540" x2="842" y2="99" stroke="#fff" stroke-width="4"/>
      <line x1="621" y1="540" x2="842" y2="118" stroke="#fff" stroke-width="3"/>
    </svg>

    <h2 class="vertical-title title-transfer">TRANSFER SWITCHES</h2>
    <div class="photo" role="img" aria-label="Automatic transfer switch enclosure product photo" style="left:92px;top:272px;width:176px;height:232px;background:linear-gradient(90deg,#a9abad,#d4d5d6 40%,#bfc0c1)"></div>

    <ul class="spec-list" style="left:114px;top:35px">
      <li>30 to 500 KW powered by Fieldmark diesel</li>
      <li>engines, EPA Tier 2, Tier 3 and Tier i4</li>
      <li>13 to 60 KW powered by Kellan diesel engines. EPA Tier i4</li>
      <li>Larocque alternators Stanwell (Cumberton</li>
      <li>Generator Technologies) alternators [optional]</li>
      <li>Deepline DL 7000 series controllers for stand-alone operation</li>
      <li>Deepline DL 8000 series controllers for</li>
      <li>paralleling operation [optional]</li>
      <li>30 to 500 KW powered by Fieldmark diesel engines. EPA Tier 2, Tier 3</li>
      <li>and Tier i4</li>
    </ul>
    <ul class="spec-list" style="left:123px;top:144px">
      <li>13 to 60 KW powered by Kellan diesel engines. EPA Tier i4</li>
      <li>Larocque alternators</li>
      <li>Stanwell (Cumberton</li>
      <li>Generator Technologies) alternators [optional]</li>
      <li>Deepline DL 7000 series controllers for stand-alone operation</li>
      <li>Deepline DL 8000 series controllers for</li>
      <li>paralleling operation [optional]</li>
      <li>Arbell manual and motorized main line circuit breaker</li>
      <li>50 to 5000-Gal, single-wall fuel tanks</li>
      <li>50 to 5000-Gal, double-walled UL142 listed fuel tanks</li>
      <li>&nbsp;Battery disconnect switch &nbsp;12V starting battery</li>
    </ul>
    <span class="page-num" style="left:18px;top:510px;color:var(--white)">PAGE 12</span>

    <h2 class="distributors-title">OUR<br>DISTRIBUTORS</h2>
    <p class="products-label">OUR PRODUCTS ARE:</p>
    <ul class="product-list">
      <li>DIESEL GENERATORS</li>
      <li>STANDBY GENERATORS</li>
      <li>PRIME GENERATORS</li>
      <li>RENTAL GENERATORS</li>
      <li>AC ALTERNATORS</li>
      <li>ALTERNATOR PARTS</li>
      <li>CONTROLLERS</li>
      <li>TRANSFER SWITCHES</li>
    </ul>
    <div class="team-photo" role="img" aria-label="Photo of a team meeting around a conference table"></div>
    <span class="page-num" style="right:16px;top:510px;color:var(--white)">PAGE 13</span>
  </section>

</main>
</body>
</html>
```